GlassHaven Artbook for Okanagan Region, British Columbia

Creating an art book: GlassHaven, for the Okanagan Wine Region in British Columbia, Canada. Would like smart, modern, clean and linear...cool, sexy urban, not ugly boring suburban... I need a cover that appeals to the wino in all of us! Title: GlassHaven -Marla Dovicki
Updates
Thank you all kindly for your efforts. I have added some files so that you can get a sense of my aesthetic...it's never easy trying to figure it out, is it? I will hopefully have dimensions of book soon...cheers, Marla
would anyone please design a giant wine bottle with the wine label that looks like a label but says glasshaven...just curious to see if it works as a design or not...thank you.
Target Market(s)
Designing this wine art book of quotes to wineries in Okanagan BC. Buyer is wine lover and tourist ready to spend his vacation bucks on this wonderful book!
Look and feel

```html
<!DOCTYPE html>
<html lang="en">
<head>
<meta charset="utf-8">
<title>GlassHaven – Okanagan Wine Region</title>
<link rel="stylesheet" href="https://fonts.googleapis.com/css2?family=Archivo+Black&family=Roboto:ital@1&display=swap">
<style>
  :root {
    --page: #ffffff;
    --cover: #231f20;
    --spine: #ececec;
    --spine-ink: #231f20;
    --spine-note: #555555;
    --merlot: #7d0a14;
    --berry: #a3005e;
    --lime: #b5d334;
    --butter: #fff68f;
    --white: #ffffff;
  }
  html, body {
    margin: 0;
    padding: 0;
    width: 1200px;
    height: 1200px;
    overflow: hidden;
    background: var(--page);
  }
  .canvas {
    position: relative;
    width: 1200px;
    height: 1200px;
  }
  .book {
    position: absolute;
    left: 270px;
    top: 100px;
    width: 661px;
    height: 1000px;
    display: block;
  }
  .spine-ground { fill: var(--spine); }
  .cover-ground { fill: var(--cover); }
  .title-letter {
    font-family: "Archivo Black", "Arial Black", sans-serif;
  }
  .letter-merlot { fill: var(--merlot); }
  .letter-berry { fill: var(--berry); }
  .letter-lime { fill: var(--lime); }
  .letter-butter { fill: var(--butter); }
  .letter-white { fill: var(--white); }
  .letter-ink { fill: var(--spine-ink); }
  .region-line {
    font-family: "Roboto", Arial, sans-serif;
    font-style: italic;
    font-size: 14px;
    fill: var(--white);
  }
  .spine-region-line {
    font-family: "Roboto", Arial, sans-serif;
    font-style: italic;
    font-size: 12px;
    fill: var(--spine-note);
  }
</style>
</head>
<body>
  <main class="canvas">
    <svg class="book" viewBox="0 0 661 1000" xmlns="http://www.w3.org/2000/svg" aria-labelledby="book-title">
      <title id="book-title">GlassHaven – Okanagan Wine Region</title>

      <g class="spine">
        <rect class="spine-ground" x="0" y="0" width="120" height="1000"/>
        <g class="spine-title">
          <text class="title-letter letter-merlot" x="30" y="195" font-size="116" textLength="60" lengthAdjust="spacingAndGlyphs">G</text>
          <text class="title-letter letter-merlot" x="30" y="285" font-size="116" textLength="60" lengthAdjust="spacingAndGlyphs">L</text>
          <text class="title-letter letter-berry" x="30" y="375" font-size="116" textLength="60" lengthAdjust="spacingAndGlyphs">A</text>
          <text class="title-letter letter-lime" x="30" y="465" font-size="116" textLength="60" lengthAdjust="spacingAndGlyphs">S</text>
          <text class="title-letter letter-butter" x="30" y="555" font-size="116" textLength="60" lengthAdjust="spacingAndGlyphs">S</text>
          <text class="title-letter letter-ink" x="24" y="605" font-size="44" textLength="72" lengthAdjust="spacingAndGlyphs">HAVEN</text>
        </g>
        <g class="spine-region">
          <text class="spine-region-line" x="60" y="900" text-anchor="middle">Okanagan</text>
          <text class="spine-region-line" x="60" y="916" text-anchor="middle">Wine Region</text>
        </g>
      </g>

      <g class="cover" transform="translate(120 0)">
        <rect class="cover-ground" x="0" y="0" width="541" height="1000"/>

        <g class="title-row title-row-top">
          <text class="title-letter letter-merlot" x="42" y="395" font-size="490" textLength="170" lengthAdjust="spacingAndGlyphs">G</text>
          <text class="title-letter letter-merlot" x="216" y="395" font-size="490" textLength="116" lengthAdjust="spacingAndGlyphs">L</text>
          <text class="title-letter letter-berry" x="345" y="395" font-size="490" textLength="154" lengthAdjust="spacingAndGlyphs">A</text>
        </g>

        <g class="region-tag">
          <text class="region-line" x="362" y="196" text-anchor="end">Okanagan</text>
          <text class="region-line" x="362" y="214" text-anchor="end">Wine Region</text>
        </g>

        <g class="title-row title-row-middle">
          <text class="title-letter letter-lime" x="42" y="723" font-size="415" textLength="224" lengthAdjust="spacingAndGlyphs">S</text>
          <text class="title-letter letter-butter" x="275" y="723" font-size="415" textLength="224" lengthAdjust="spacingAndGlyphs">S</text>
        </g>

        <g class="title-row title-row-bottom">
          <text class="title-letter letter-white" x="42" y="937" font-size="288" textLength="457" lengthAdjust="spacingAndGlyphs">HAVEN</text>
        </g>
      </g>
    </svg>
  </main>
</body>
</html>
```